Northfield Builders Guild Business card

We are looking for a new business card design with photo included.
Our business is a nonprofit construction contractor membership organization. We offer business education, assist with business setup and licensing, provide safety training, and provide a member directory.
URL: www.builderslinkguild.org
Color code:
CMYK: 0 cyan, 42 magenta, 100 yellow, 0 black for Print.
Hexidecimal: #FF9900
RGB: R 255; G 153; B 0

```html
<!DOCTYPE html>
<html lang="en">
<head>
<meta charset="utf-8">
<title>Northfield Builders Guild – Business Card</title>
<link href="https://fonts.googleapis.com/css2?family=Montserrat:wght@500;600;800&family=Arimo:wght@400&display=swap" rel="stylesheet">
<style>
  :root{
    --orange:#FF9900;
    --ink:#2d2d2f;
    --card-dark:#161616;
    --card-dark-soft:#222222;
    --paper:#ffffff;
    --stage:#c4c4c4;
    --rule:#9a9a9a;
  }
  *{margin:0;padding:0;box-sizing:border-box}
  html,body{width:1200px;height:1200px;overflow:hidden}
  body{background:var(--stage);position:relative;font-family:'Montserrat',sans-serif}
  .card{position:absolute;top:303px;width:370px;height:594px;overflow:hidden}
  .card--back{left:216px;background:var(--card-dark)}
  .card--front{left:614px;background:var(--paper)}

  .card__pattern{position:absolute;inset:0;
    background:radial-gradient(circle at 50% 45%,var(--card-dark-soft) 0%,var(--card-dark) 70%)}

  .wordmark{position:absolute;left:0;right:0;text-align:center;font-family:'Montserrat',sans-serif;font-weight:800;line-height:1.02}
  .wordmark__main{display:block;font-size:34px;letter-spacing:-0.5px}
  .wordmark__sub{display:block;font-size:14px;letter-spacing:9px;margin-top:6px;padding-left:9px}
  .card--back .wordmark{top:118px;color:#ffffff}
  .card--front .wordmark{top:126px;color:var(--ink)}
  .wordmark__dot{display:inline-block;width:12px;height:12px;border-radius:50%;background:var(--orange);margin-left:6px;vertical-align:middle}

  .services{position:absolute;top:390px;left:0;right:0;text-align:center;list-style:none;
    font-family:'Arimo',sans-serif;color:#fff;font-size:15px;line-height:22px}
  .services li{margin-bottom:16px}

  .person{position:absolute;top:306px;left:0;right:0;text-align:center}
  .person__name{font-weight:600;font-size:22px;color:var(--ink)}
  .person__title{font-weight:500;font-size:14.5px;color:var(--orange);margin-top:2px}

  .icon-row{position:absolute;top:363px;left:88px;width:190px;height:22px}
  .contact{position:absolute;top:398px;left:0;right:0;text-align:center;font-family:'Arimo',sans-serif;
    font-size:16px;line-height:22.5px;color:var(--ink);letter-spacing:0.3px}
  .accent{color:var(--orange)}
  .contact-rule{position:absolute;top:515px;left:88px;width:194px;height:1px;background:var(--rule)}
  .address{position:absolute;top:524px;left:0;right:0;text-align:center;font-weight:500;font-size:16.5px;line-height:21.5px;color:var(--ink)}
</style>
</head>
<body>
  <section class="card card--back">
    <div class="card__pattern" role="img" aria-label="Faint decorative pattern of concentric rings on the dark card back"></div>
    <div class="wordmark">
      <span class="wordmark__main">NORTHFIELD</span>
      <span class="wordmark__main">BUILDERS</span>
      <span class="wordmark__sub">GUILD</span>
    </div>
    <ul class="services">
      <li>BUSINESS EDUCATION</li>
      <li>ASSIST WITH BUSINESS SETUP<br>AND LICENSING</li>
      <li>PROVIDE SAFETY TRAINING</li>
      <li>PROVIDE A MEMBER DIRECTORY</li>
    </ul>
  </section>

  <section class="card card--front">
    <div class="wordmark">
      <span class="wordmark__main">NORTHFIELD</span>
      <span class="wordmark__main">BUILDERS</span>
      <span class="wordmark__sub">GUILD<span class="wordmark__dot"></span></span>
    </div>

    <div class="person">
      <div class="person__name">DANIEL HARPER</div>
      <div class="person__title">MANAGING DIRECTOR</div>
    </div>

    <svg class="icon-row" viewBox="0 0 190 22" aria-hidden="true">
      <line x1="0" y1="11" x2="36" y2="11" stroke="#9a9a9a" stroke-width="1"/>
      <line x1="154" y1="11" x2="190" y2="11" stroke="#9a9a9a" stroke-width="1"/>
      <g fill="#FF9900">
        <circle cx="48" cy="11" r="10.5"/><circle cx="71.5" cy="11" r="10.5"/>
        <circle cx="95" cy="11" r="10.5"/><circle cx="118.5" cy="11" r="10.5"/>
        <circle cx="142" cy="11" r="10.5"/>
      </g>
      <g fill="none" stroke="#fff" stroke-width="1.3" stroke-linecap="round" stroke-linejoin="round">
        <path d="M44 6.5c-1 1-1 3 1 5.5s4.5 3 5.5 2l1-1.2-2-1.6-1 .8c-1-.5-2-1.5-2.5-2.5l.8-1-1.6-2z"/>
        <rect x="68" y="5.5" width="7" height="11" rx="1"/><line x1="70.5" y1="14.5" x2="72.5" y2="14.5"/>
        <rect x="91" y="5.5" width="8" height="3"/><rect x="89.5" y="8.5" width="11" height="5" rx="1"/><rect x="91.5" y="12" width="7" height="4"/>
        <rect x="113" y="7" width="11" height="8" rx="1"/><path d="M113 7.5l5.5 4.5 5.5-4.5"/>
        <circle cx="142" cy="11" r="5.5"/><ellipse cx="142" cy="11" rx="2.5" ry="5.5"/><line x1="136.5" y1="11" x2="147.5" y2="11"/>
      </g>
    </svg>

    <div class="contact">
      (541) 382-7716 <span class="accent">(Office)</span><br>
      800-555-0148<br>
      541.382.0932<br>
      support@nbguild.org<br>
      www.<span class="accent">builderslinkguild</span>.org
    </div>
    <div class="contact-rule"></div>
    <div class="address">2400 Cedar Ridge Rd<br>Suite #210, Salem, OR 97301</div>
  </section>
</body>
</html>
```